We need a logo for our business which is a dental clinic (i.e. dentistry).
We would lilke designs using the colour blue, green and black incorporating the words Corvath Dental, possibly a smile or a tooth image can be considered for incorporation in the logo.

Industry/Entity Type

Dental

```html
<!DOCTYPE html>
<html lang="en">
<head>
<meta charset="utf-8">
<title>Corvath Dental – Business Card</title>
<link rel="stylesheet" href="https://fonts.googleapis.com/css2?family=Open+Sans:wght@400;600&display=swap">
<style>
  :root {
    --page-bg: #cdc6be;
    --card-top: #e4dfd8;
    --card-band: #2e4e6b;
    --brand-dot: #2a4d74;
    --brand-text: #3a3632;
    --name-blue: #3b5a80;
    --role-grey: #4a4a4a;
    --band-text: #dde3ea;
    --phone-text: #b07a78;
    --email-text: #d8c4bd;
    --icon-colour: #c9d2dc;
  }
  * { margin: 0; padding: 0; box-sizing: border-box; }
  html, body {
    width: 1200px; height: 970px; overflow: hidden;
    background: var(--page-bg);
    font-family: "Open Sans", Arial, sans-serif;
  }
  .canvas { position: relative; width: 1200px; height: 970px; }
  .card {
    position: absolute; left: 100px; top: 207px;
    width: 1000px; height: 556px;
    background: var(--card-top);
    box-shadow: 0 12px 30px rgba(0,0,0,0.18);
    overflow: hidden;
  }
  .brand {
    position: absolute; left: 660px; top: 29px; width: 342px;
    display: flex; flex-direction: column; align-items: center;
  }
  .brand-dot {
    width: 117px; height: 117px; border-radius: 50%;
    background: var(--brand-dot);
  }
  .brand-name {
    margin-top: 8px;
    font-size: 31px; font-weight: 400; letter-spacing: 1.5px;
    text-transform: uppercase; color: var(--brand-text);
    white-space: nowrap;
  }
  .person { position: absolute; left: 56px; top: 244px; }
  .person-name { font-size: 34px; font-weight: 400; color: var(--name-blue); line-height: 1.1; }
  .person-role { font-size: 27px; color: var(--role-grey); line-height: 1.15; }
  .contact-band {
    position: absolute; left: 0; top: 331px; width: 100%; height: 225px;
    background: var(--card-band);
  }
  .contact-list { position: absolute; left: 54px; top: 12px; list-style: none; }
  .contact-item {
    display: flex; align-items: flex-start;
    font-size: 29px; line-height: 37px; color: var(--band-text);
    margin-bottom: 6px; white-space: nowrap;
  }
  .contact-item .icon { width: 42px; height: 37px; flex: none; margin-right: 18px; }
  .contact-item.phone { color: var(--phone-text); }
  .contact-item.email { color: var(--email-text); }
</style>
</head>
<body>
<div class="canvas">
  <div class="card">
    <div class="brand">
      <div class="brand-dot"></div>
      <div class="brand-name">Corvath Dental</div>
    </div>

    <div class="person">
      <div class="person-name">Mara Ellison</div>
      <div class="person-role">Dentist</div>
    </div>

    <div class="contact-band">
      <ul class="contact-list">
        <li class="contact-item address">
          <svg class="icon" viewBox="0 0 42 37" aria-hidden="true">
            <path d="M21 5 L38 20 L33 20 L33 33 L25 33 L25 25 L17 25 L17 33 L9 33 L9 20 L4 20 Z" fill="var(--icon-colour)"/>
          </svg>
          <span>48 Harbor Lane<br>Oregon, USA</span>
        </li>
        <li class="contact-item phone">
          <svg class="icon" viewBox="0 0 42 37" aria-hidden="true">
            <circle cx="21" cy="18" r="13" fill="none" stroke="var(--icon-colour)" stroke-width="2"/>
            <path d="M16 12 q-2 7 8 13 l3 -3 l-3 -3 l-2 2 q-3 -2 -4 -5 l2 -2 l-2 -3 Z" fill="var(--icon-colour)"/>
          </svg>
          <span>555-014-2210</span>
        </li>
        <li class="contact-item phone">
          <svg class="icon" viewBox="0 0 42 37" aria-hidden="true">
            <rect x="15" y="4" width="12" height="28" rx="2" fill="none" stroke="var(--icon-colour)" stroke-width="2"/>
            <rect x="17.5" y="8" width="7" height="8" fill="var(--icon-colour)"/>
            <circle cx="21" cy="26" r="2" fill="var(--icon-colour)"/>
          </svg>
          <span>555-014-2211</span>
        </li>
        <li class="contact-item email">
          <svg class="icon" viewBox="0 0 42 37" aria-hidden="true">
            <circle cx="21" cy="18" r="13" fill="none" stroke="var(--icon-colour)" stroke-width="2"/>
            <rect x="13" y="12" width="16" height="12" fill="none" stroke="var(--icon-colour)" stroke-width="1.8"/>
            <path d="M13 12 L21 19 L29 12" fill="none" stroke="var(--icon-colour)" stroke-width="1.8"/>
          </svg>
          <span>mara@corvath.example</span>
        </li>
      </ul>
    </div>
  </div>
</div>
</body>
</html>
```